IT Company requires new Business Card design.

Over the years we have had a few different business card designs. We are now due for new cards across the board for all staff. We felt this would be a good time to start fresh with a new design. Our traditional card simply had our details on the front, and a list of services on the back. We don't particularly need the list of services, we have had cards where the only thing on the rear of the card was our logo.
Feel free to be creative, we would like our tag line "Complete IT Management" to appear at some point, doesn't necessarily have to be with the logo.
I have attached samples and drafts of various previous cards we have used over the years.

```html
<!DOCTYPE html>
<html lang="en">
<head>
<meta charset="utf-8">
<title>Ridgeline Systems – Business Card</title>
<link rel="stylesheet" href="https://fonts.googleapis.com/css2?family=Open+Sans:wght@400;600;800&display=swap">
<style>
  :root {
    --backdrop: #e6e4e0;
    --card: #ffffff;
    --slate: #5b6b79;
    --ink: #4a4f55;
    --rule: #9aa3ab;
    --shadow: rgba(40, 40, 40, 0.18);
  }
  html, body {
    margin: 0;
    padding: 0;
    overflow: hidden;
  }
  body {
    width: 1200px;
    height: 720px;
    background: var(--backdrop);
    font-family: "Open Sans", Arial, sans-serif;
    position: relative;
  }
  .card {
    position: absolute;
    width: 540px;
    height: 309px;
    background: var(--card);
    box-shadow: 0 6px 18px var(--shadow);
    box-sizing: border-box;
  }
  .card--front { left: 40px; top: 120px; }
  .card--back  { left: 620px; top: 290px; }

  /* Front */
  .brand {
    position: absolute;
    left: 36px;
    top: 40px;
    display: flex;
    align-items: center;
    gap: 12px;
    color: var(--slate);
  }
  .brand__square {
    width: 24px;
    height: 24px;
    background: var(--slate);
  }
  .brand__name {
    font-weight: 800;
    font-size: 32px;
    line-height: 1;
    letter-spacing: 0.5px;
    text-transform: uppercase;
  }
  .person {
    position: absolute;
    left: 68px;
    top: 158px;
    color: var(--ink);
  }
  .person__name {
    margin: 0;
    font-weight: 600;
    font-size: 17px;
    color: var(--slate);
  }
  .person__role {
    margin: 2px 0 0;
    font-size: 13px;
  }
  .front__web {
    position: absolute;
    left: 68px;
    bottom: 30px;
    margin: 0;
    font-size: 15px;
    letter-spacing: 0.6px;
    color: var(--ink);
  }
  .divider {
    position: absolute;
    left: 300px;
    top: 112px;
    width: 1px;
    height: 150px;
    background: var(--rule);
  }
  .contact {
    position: absolute;
    left: 316px;
    top: 112px;
    margin: 0;
    padding: 0;
    list-style: none;
    font-size: 12.5px;
    color: var(--ink);
  }
  .contact li {
    display: flex;
    align-items: center;
    gap: 7px;
    height: 19px;
  }
  .contact svg {
    width: 12px;
    height: 12px;
    fill: var(--slate);
    flex: none;
  }
  .address {
    position: absolute;
    left: 316px;
    top: 202px;
    margin: 0;
    font-style: normal;
    font-size: 12.5px;
    line-height: 18px;
    color: var(--ink);
  }
  .tagline {
    position: absolute;
    left: 316px;
    bottom: 32px;
    margin: 0;
    font-weight: 600;
    font-size: 10px;
    letter-spacing: 1.6px;
    text-transform: uppercase;
    color: var(--slate);
  }

  /* Back */
  .back__brand {
    position: absolute;
    left: 0;
    right: 0;
    top: 104px;
    display: flex;
    align-items: center;
    justify-content: center;
    gap: 14px;
    color: var(--slate);
  }
  .back__square {
    width: 32px;
    height: 32px;
    background: var(--slate);
  }
  .back__name {
    font-weight: 800;
    font-size: 40px;
    line-height: 1;
    letter-spacing: 1px;
    text-transform: uppercase;
  }
  .back__web {
    position: absolute;
    left: 0;
    right: 0;
    bottom: 34px;
    margin: 0;
    text-align: center;
    font-size: 16px;
    letter-spacing: 1px;
    color: var(--ink);
  }
</style>
</head>
<body>

<section class="card card--front" aria-label="Card front">
  <div class="brand">
    <span class="brand__square"></span>
    <span class="brand__name">Ridgeline Systems</span>
  </div>

  <div class="person">
    <p class="person__name">Daniel Morrow</p>
    <p class="person__role">Operation Manager</p>
  </div>

  <p class="front__web">www.ridgelinesys.com.au</p>

  <span class="divider"></span>

  <ul class="contact">
    <li>
      <svg viewBox="0 0 12 12" aria-hidden="true"><path d="M2.5 0.8 4.3 2.9 3.4 4.2c.7 1.6 2 2.9 3.6 3.6l1.3-.9 2.1 1.8-.9 2C5.3 10.3 1.5 6.5 1 2z"/></svg>
      08 5550 1427
    </li>
    <li>
      <svg viewBox="0 0 12 12" aria-hidden="true"><path d="M3.5 0h5a1 1 0 0 1 1 1v10a1 1 0 0 1-1 1h-5a1 1 0 0 1-1-1V1a1 1 0 0 1 1-1zm.5 1.5v7h4v-7zM6 9.6a.8.8 0 1 0 0 1.6.8.8 0 0 0 0-1.6z"/></svg>
      0400 555 218
    </li>
    <li>
      <svg viewBox="0 0 12 12" aria-hidden="true"><path d="M3 0h6v3.5H3zM1 4.5h10a1 1 0 0 1 1 1V10H0V5.5a1 1 0 0 1 1-1zm2 3.5v4h6V8z"/></svg>
      08 5550 1428
    </li>
    <li>
      <svg viewBox="0 0 12 12" aria-hidden="true"><path d="M0 2h12v8H0zm1.2 1.1v.3L6 6.6l4.8-3.2v-.3zM1.2 4.8v4h9.6v-4L6 8z"/></svg>
      daniel@ridgelinesys.com.au
    </li>
  </ul>

  <address class="address">
    Unit 7 21 Marlin Way<br>
    Bayview WA 6000
  </address>

  <p class="tagline">Complete IT Management</p>
</section>

<section class="card card--back" aria-label="Card back">
  <div class="back__brand">
    <span class="back__square"></span>
    <span class="back__name">Ridgeline Systems</span>
  </div>
  <p class="back__web">www.ridgelinesys.com.au</p>
</section>

</body>
</html>
```